I need a business card designed using the logo provided either vertical or horizontal......Harbourline Property Group is an Australian based real estate company that caters for the upper end of the market so the design of the business card "must reflect" the companies image!!
Colour combinations are optional but "must be realistic" and must be able to be accurately useable CMYK colours.
Please consider that any colours used "must be able to be used" and be suitable in following designs for "pull out banner signs" and "real estate signs".
The colours and the font in the attached designs are for example and other combinations are encouraged.
Target Market(s)
The High End of the Australian real estate market
Industry/Entity Type
Business
Contact Information for Business Card
Logo - Business Name - Director + Licensed Real Estate Agent - Mobile Number (Cell Phone) - Business Number - Fax - Email Address - Web address
Requirements
Must have
- Designs and colours (CMYK) that can easily be interpreted by an Australian printer.
Nice to have
- Some alternative ideas on colour and font..........the ones provided are ok and have been provided as an example but I am looking for alternative ideas
Should not have
- Loud, overly bright colours. Designs that do not reflect the professional standards of the business.
- Designs that look good on a computer monitor but can not be re-created on a printing press.............this is most important when it comes to shading etc.

```html
<!DOCTYPE html>
<html lang="en">
<head>
<meta charset="utf-8">
<title>Harbourline Property Group – Business Card</title>
<link rel="stylesheet" href="https://fonts.googleapis.com/css2?family=Roboto+Condensed:wght@400;700&display=swap">
<style>
  :root {
    --backdrop: #e9e7e3;
    --card: #fbfbfa;
    --ink: #3a3a3a;
    --ink-soft: #4a4a4a;
    --gold: #c9a83a;
    --gold-deep: #b8962c;
    --band: #231f20;
    --rule: #2e2e2e;
  }
  * { margin: 0; padding: 0; box-sizing: border-box; }
  html, body { width: 1200px; height: 892px; overflow: hidden; }
  body {
    background: var(--backdrop);
    font-family: "Roboto Condensed", "Arial Narrow", sans-serif;
    color: var(--ink);
    position: relative;
  }
  .card {
    position: absolute;
    left: 120px; top: 172px;
    width: 960px; height: 548px;
    background: linear-gradient(135deg, #ffffff 0%, var(--card) 55%, #f1f1ef 100%);
    overflow: hidden;
    box-shadow: 0 6px 24px rgba(0,0,0,0.18);
  }
  .brand {
    position: absolute;
    left: 56px; top: 180px;
    width: 340px;
    display: flex; align-items: center; gap: 18px;
  }
  .brand-square {
    width: 40px; height: 40px;
    background: var(--gold);
    flex: none;
  }
  .brand-name {
    font-weight: 700;
    font-size: 30px;
    line-height: 1.1;
    letter-spacing: 2px;
    text-transform: uppercase;
    color: var(--ink);
    white-space: nowrap;
  }
  .divider {
    position: absolute;
    left: 430px; top: 62px;
    width: 2px; height: 330px;
    background: var(--rule);
  }
  .contact {
    position: absolute;
    left: 485px; top: 70px;
  }
  .person-name {
    font-weight: 700;
    font-size: 46px;
    color: var(--gold);
    line-height: 1;
  }
  .person-role {
    font-size: 17px;
    color: var(--ink-soft);
    margin-top: 6px;
  }
  .details {
    list-style: none;
    margin-top: 40px;
    font-size: 25px;
    line-height: 33px;
    color: var(--ink);
  }
  .details li { display: flex; align-items: flex-start; }
  .details .icon {
    width: 22px; height: 33px; flex: none;
    margin-right: 14px;
    display: flex; align-items: center; justify-content: center;
  }
  .details .icon svg { width: 16px; height: 16px; }
  .details .address { display: block; }
  .band {
    position: absolute;
    left: 0; bottom: 0;
    width: 100%; height: 92px;
    background: linear-gradient(180deg, #2d2829 0%, var(--band) 100%);
  }
  .gold-tab {
    position: absolute;
    left: 0; bottom: 0;
    width: 400px; height: 116px;
    background: linear-gradient(180deg, var(--gold) 0%, var(--gold-deep) 100%);
    border-top-right-radius: 22px;
  }
</style>
</head>
<body>
  <div class="card">
    <div class="band"></div>
    <div class="gold-tab"></div>

    <div class="brand">
      <span class="brand-square"></span>
      <div class="brand-name">Harbourline<br>Property Group</div>
    </div>

    <div class="divider"></div>

    <div class="contact">
      <div class="person-name">Employee name</div>
      <div class="person-role">Managing Director</div>
      <ul class="details">
        <li>
          <span class="icon"><svg viewBox="0 0 16 16"><path fill="#c9a83a" d="M3.6 1.2l2.4 2.6-1.3 1.8c.9 2 2.7 3.8 4.7 4.7l1.8-1.3 2.6 2.4-1.4 2.2C7 13.4 2.6 9 1.4 3l2.2-1.8z"/></svg></span>
          <span>0412 555 018</span>
        </li>
        <li>
          <span class="icon"><svg viewBox="0 0 16 16"><rect x="1" y="3" width="14" height="10" fill="#c9a83a"/><path d="M1.5 3.5L8 9l6.5-5.5" fill="none" stroke="#fff" stroke-width="1.3"/></svg></span>
          <span>info@harbourline.example</span>
        </li>
        <li>
          <span class="icon"><svg viewBox="0 0 16 16"><circle cx="8" cy="8" r="7" fill="#c9a83a"/><path d="M1 8h14M8 1c-3 3.5-3 10.5 0 14M8 1c3 3.5 3 10.5 0 14" fill="none" stroke="#fff" stroke-width="1"/></svg></span>
          <span>www.harbourline.example</span>
        </li>
        <li>
          <span class="icon"></span>
          <span class="address">Level 4, 18 Wharf Road<br>Pyrmont NSW 2009</span>
        </li>
      </ul>
    </div>
  </div>
</body>
</html>
```